Stationery Design + Business Cards

Stationary (letterhead as A4 210x297mm and Letter 8.5"x11", preferably both master page + 2nd pages)

Also need business cards, standard size 50x88mm, can be vertical or horizontal.

You can use a front/back design for the business cards, or front only.

Looking at the uploaded file (devank, you already have that), I want it to use the first logo on the list (4 colors).

Alternative, try the grayscale version (second file).

I need the following information on the business card (in no particular order, let me know what you come up with): 

Firstname Lastlame 
Title 

Mobile +1 555-204-7391 

VelaMorn, Inc. 
24851 Birchwood Ridge Passage 
Linden Falls, OH 46099 
Tel. +1 555-368-4172 
Fax +1 555-619-0834 

Web: www.velamorn.example 
Twitter: twitter/VelaMorn or @VelaMorn 
Facebook: facebook.com/VelaMorn 

For letterhead, just the company name, address + phone number & fax number 

If you think the phone/fax or something else should not be on the business cards, or something could be missing, let me know.

```html
<!DOCTYPE html>
<html lang="en">
<head>
<meta charset="utf-8">
<title>VelaMorn Letterhead</title>
<link rel="stylesheet" href="https://fonts.googleapis.com/css2?family=Open+Sans:wght@400;700&display=swap">
<style>
  :root {
    --backdrop: #000000;
    --paper: #ffffff;
    --brand-blue: #1b4ea3;
    --tint-grey: #eceeee;
    --label-white: #ffffff;
  }
  html, body {
    margin: 0;
    padding: 0;
    width: 900px;
    height: 1200px;
    overflow: hidden;
    background: var(--backdrop);
    font-family: "Open Sans", Arial, sans-serif;
  }
  .sheet-label {
    position: absolute;
    top: 26px;
    left: 0;
    width: 900px;
    text-align: center;
    color: var(--label-white);
    font-weight: 700;
    font-size: 17px;
    margin: 0;
  }
  .letterhead {
    position: absolute;
    left: 60px;
    top: 58px;
    width: 786px;
    height: 1111px;
    background: var(--paper);
    overflow: hidden;
  }
  .brand {
    position: absolute;
    left: 60px;
    top: 76px;
    display: flex;
    align-items: center;
    gap: 24px;
  }
  .brand-dot {
    width: 32px;
    height: 32px;
    border-radius: 50%;
    background: var(--brand-blue);
  }
  .brand-name {
    font-size: 46px;
    font-weight: 400;
    color: var(--brand-blue);
    line-height: 1;
    letter-spacing: -0.8px;
  }
  .company-address {
    position: absolute;
    left: 443px;
    top: 92px;
    padding-left: 10px;
    border-left: 1px solid var(--brand-blue);
    color: var(--brand-blue);
    font-weight: 700;
    font-size: 10px;
    line-height: 15px;
    margin: 0;
    font-style: normal;
    white-space: nowrap;
  }
  .corner-accent {
    position: absolute;
    left: 0;
    top: 0;
    width: 786px;
    height: 1111px;
    pointer-events: none;
  }
</style>
</head>
<body>
  <p class="sheet-label">Letter Head 210x297mm</p>
  <main class="letterhead">
    <svg class="corner-accent" viewBox="0 0 786 1111" aria-hidden="true">
      <circle cx="690" cy="1000" r="250" fill="var(--tint-grey)"/>
    </svg>
    <div class="brand">
      <span class="brand-dot"></span>
      <span class="brand-name">VelaMorn</span>
    </div>
    <address class="company-address">
      VelaMorn, Inc., 24851 Birchwood Ridge Passage,<br>
      Linden Falls, OH 46099, Tel. +1 555-368-4172, Fax +1 555-619-0834
    </address>
  </main>
</body>
</html>
```